Design and Renovation Company Luxury Business Card

I want to create a luxury business card for a Design and Renovation Firm . We will use our current logo. The company name is 528BUILDA. We do not want anything standard. We need a very unique concept.
Please see uploaded inspiration. I really like the textured paper option. I would like the card to be thick with debossing, and/or embossing options. The logo has orange in it but I would like to see the card with and without the orange. I think the orange may make the company feel less high-end. The goal is to elevate the logo not match its vibe per se of the logo. We want something very unique, not standard at all!
I would like a space for :
Logo,
Name,
Position,
Email,
Office number,
Website Address,
Business Address,
Thank you!
Have fun!
Target Market(s)
Home owners Age 35 +
Industry/Entity Type
Design and Renovation
Contact Information for Business Card
Logo, Name, Position, Email, Office number, Website Address, Business Address,.
Colors
Designer to choose colors to be used in the design.
Requirements
Must have
- A luxury designer feel. Must be black or dark grey but open to other luxury ideas.
Nice to have
- Gold, silver, black embossing or debossing. Textured paper design.
Should not have
- A cheap look and feel.

```html
<!DOCTYPE html>
<html lang="en">
<head>
<meta charset="utf-8">
<title>528BUILDA Business Card</title>
<link rel="stylesheet" href="https://fonts.googleapis.com/css2?family=Lexend:wght@400;500;600;700&display=swap">
<style>
  :root {
    --page-bg: #cccccc;
    --card-charcoal: #161616;
    --ink-light: #f2f2f2;
    --silver: #b9b9b9;
    --muted: #9c9c9c;
    --stone-dark: #121212;
    --stone-mid: #262626;
    --stone-vein: #3c3c3c;
  }
  * { margin: 0; padding: 0; box-sizing: border-box; }
  html, body {
    width: 1200px;
    height: 1112px;
    overflow: hidden;
    background: var(--page-bg);
    font-family: "Lexend", sans-serif;
  }
  .canvas { position: relative; width: 1200px; height: 1112px; }

  .stone {
    background: linear-gradient(120deg, var(--stone-dark) 0%, var(--stone-mid) 30%, var(--stone-dark) 52%, var(--stone-vein) 74%, var(--stone-mid) 86%, var(--stone-dark) 100%);
  }

  .card-front {
    position: absolute;
    left: 75px; top: 75px;
    width: 753px; height: 443px;
  }
  .brand {
    position: absolute;
    left: 263px; top: 178px;
    display: flex;
    align-items: flex-end;
    gap: 12px;
  }
  .brand-square {
    width: 40px; height: 40px;
    background: var(--silver);
    margin-bottom: 8px;
  }
  .brand-text { display: flex; flex-direction: column; }
  .brand-name {
    font-weight: 500;
    font-size: 62px;
    line-height: 1;
    letter-spacing: 2px;
    color: var(--ink-light);
  }
  .brand-tagline {
    margin-top: 8px;
    font-weight: 500;
    font-size: 17px;
    letter-spacing: 5px;
    color: var(--silver);
  }

  .card-back {
    position: absolute;
    left: 372px; top: 594px;
    width: 753px; height: 443px;
    background: var(--card-charcoal);
  }
  .card-back .stone-panel {
    position: absolute;
    right: 0; top: 0;
    width: 225px; height: 100%;
  }
  .person-name {
    position: absolute;
    left: 45px; top: 44px;
    font-weight: 700;
    font-size: 49px;
    line-height: 1;
    color: var(--ink-light);
  }
  .person-role {
    position: absolute;
    left: 45px; top: 97px;
    font-weight: 400;
    font-size: 34px;
    line-height: 1;
    color: var(--silver);
  }
  .contact-list {
    position: absolute;
    left: 76px; top: 245px;
    list-style: none;
    font-size: 20px;
    line-height: 31.5px;
    color: var(--muted);
  }
  .contact-list li { position: relative; }
  .contact-list li::before {
    content: "";
    position: absolute;
    left: -22px; top: 13px;
    width: 5px; height: 5px;
    border-radius: 50%;
    background: var(--muted);
  }
</style>
</head>
<body>
<div class="canvas">
  <section class="card-front stone" role="img" aria-label="Dark grey marble stone texture background">
    <div class="brand">
      <div class="brand-square"></div>
      <div class="brand-text">
        <span class="brand-name">528BUILDA</span>
        <span class="brand-tagline">Design and Renovation Firm</span>
      </div>
    </div>
  </section>

  <section class="card-back">
    <h1 class="person-name">Your Name</h1>
    <p class="person-role">Company Manager</p>
    <ul class="contact-list">
      <li>(555) 014-2290</li>
      <li>info@528builda.com</li>
      <li>www.528builda.ca</li>
      <li>12 Harrow Crest Drive Brampton,<br>Ontario Canada L6R 2K4</li>
    </ul>
    <div class="stone-panel stone" role="img" aria-label="Dark grey marble stone texture panel"></div>
  </section>
</div>
</body>
</html>
```